Home Remodeler Needs a Website!

Single page (plus contact form) website for small home remodeling company. He's got a few pictures he'd like on the site and needs some basic text. He likes clean, simple designs and is "more traditional" in his stylistic preferences. Most of his business comes from word-of-mouth advertising and so the site is just something he needs for people to feel more comfortable with his business.

Target Market(s)

People who want to remodel their homes

Coding

Coded - Design and coding required

Number of Pages Required

2 page

Requirements
Must have
• Main page to include some or all of the attached images, contact page. Neutral colors. Old domain: lindcroftmeadowbuild.com New domain: qm-ventureworks.com You can pull text from the old site or update it.
Should not have
• No loud colors/loud visual elements

```html
<!DOCTYPE html>
<html lang="en">
<head>
<meta charset="utf-8">
<title>Lindcroft Meadow Homes</title>
<link href="https://fonts.googleapis.com/css2?family=Montserrat:wght@400;600;700;800&family=Open+Sans:wght@400;600&display=swap" rel="stylesheet">
<style>
:root{
  --orange:#ea7a2c;
  --orange-deep:#d9661a;
  --charcoal:#2b2b2b;
  --ink:#1e1e1e;
  --grey:#555;
  --light:#f3f3f3;
  --field:#fbe3d1;
  --white:#fff;
}
*{margin:0;padding:0;box-sizing:border-box}
html,body{width:1200px;height:3256px;overflow:hidden;background:var(--white)}
body{position:relative;font-family:"Open Sans",sans-serif;color:var(--grey)}
.abs{position:absolute}
.heading{font-family:"Montserrat",sans-serif;font-weight:700;color:var(--ink);letter-spacing:1px}

/* header */
.site-header{top:0;left:0;width:1200px;height:52px;background:var(--white)}
.brand{left:28px;top:15px;font-family:"Montserrat",sans-serif;font-weight:700;font-size:21px;color:var(--ink);letter-spacing:.5px}
.main-nav{left:410px;top:19px;display:flex;gap:58px;font-family:"Montserrat",sans-serif;font-size:13px;font-weight:600;color:var(--ink)}
.header-phone{left:940px;top:12px;display:flex;align-items:center;gap:12px;font-family:"Montserrat",sans-serif;font-weight:600;font-size:22px;color:var(--ink)}
.phone-dot{width:30px;height:30px;border-radius:50%;background:var(--ink);display:flex;align-items:center;justify-content:center}

/* hero */
.hero-photo{top:52px;left:0;width:1200px;height:780px;background:linear-gradient(120deg,#4a4036 0%,#8b8a86 35%,#c9c6c0 55%,#5c5853 75%,#2f4a66 100%)}
.hero-badge{left:80px;top:160px;width:480px;height:480px;border-radius:50%;background:var(--orange);display:flex;flex-direction:column;align-items:center;justify-content:center;text-align:center}
.hero-ring{left:64px;top:144px;width:512px;height:512px;border-radius:50%;border:4px solid var(--orange)}
.hero-title{font-family:"Montserrat",sans-serif;font-weight:800;font-size:50px;line-height:58px;color:var(--white);letter-spacing:1px}
.btn{display:inline-block;border-radius:40px;font-family:"Montserrat",sans-serif;font-weight:700;letter-spacing:1px}
.btn-light{background:var(--white);color:var(--ink);font-size:16px;padding:12px 34px;margin-top:30px}
.hero-arrow{top:395px;width:20px;height:40px}
.scroll-label{left:560px;top:660px;width:80px;text-align:center;font-family:"Montserrat",sans-serif;font-size:13px;color:var(--white);letter-spacing:2px}

/* welcome */
.welcome{top:868px;left:0;width:1200px;text-align:center}
.welcome h1{font-size:34px;line-height:42px}
.welcome p{width:880px;margin:22px auto 0;font-size:13.5px;line-height:19px;color:var(--grey)}

/* services */
.services-band{top:1130px;left:0;width:1200px;height:780px}
.services-title{left:120px;top:1390px;font-size:32px;line-height:40px;color:var(--white)}
.service-list{top:1500px;font-size:14px;line-height:24px;color:var(--white);list-style:none}
.services-copy{left:120px;top:1620px;width:460px;font-size:13px;line-height:22px;color:#d8d8d8}
.btn-book{left:120px;top:1728px;background:var(--white);color:var(--ink);font-size:14px;padding:12px 30px}
.services-photo{left:730px;top:1330px;width:380px;height:380px;border-radius:50%;background:radial-gradient(circle at 40% 40%,#8a6b4d,#3d2a1d 70%);border:8px solid #555}

/* projects */
.projects-title{top:1950px;left:0;width:1200px;text-align:center;font-size:38px}
.project{top:2048px;height:264px;display:flex;align-items:center;justify-content:center;font-family:"Montserrat",sans-serif;font-weight:700;font-size:24px;color:var(--white);letter-spacing:1px}
.dots{top:2336px;left:0;width:1200px;display:flex;flex-direction:column;align-items:center;gap:8px}
.dot-row{display:flex;gap:10px}
.dot{width:12px;height:12px;border-radius:50%;background:#bbb}
.dot.on{background:var(--ink)}

/* contact */
.contact-band{top:2428px;left:0;width:1200px;height:640px}
.contact-title{top:2500px;left:0;width:1200px;text-align:center;font-size:38px;color:var(--white)}
.contact-phones{top:2580px;left:0;width:1200px;display:flex;justify-content:center;gap:100px;font-family:"Montserrat",sans-serif;font-weight:700;font-size:22px;color:var(--white)}
.contact-phones span{display:flex;align-items:center;gap:12px}
.field{background:var(--field);border-radius:4px;font-size:13px;color:#9b8576;padding:10px 14px}
.btn-send{left:500px;top:2912px;width:200px;height:52px;background:var(--ink);color:var(--white);font-size:18px;display:flex;align-items:center;justify-content:center}

/* footer */
.footer-nav{top:3092px;left:0;width:1200px;display:flex;justify-content:center;gap:130px;font-family:"Montserrat",sans-serif;font-weight:700;font-size:15px;color:var(--ink)}
.copyright{top:3140px;left:0;width:1200px;text-align:center;font-size:13px;color:var(--grey)}
.social{top:3180px;left:0;width:1200px;display:flex;justify-content:center;gap:18px}
.social span{width:36px;height:36px;border-radius:50%;background:#7a7a7a}
</style>
</head>
<body>

<header class="abs site-header">
  <div class="abs brand">LINDCROFT MEADOW HOMES</div>
  <nav class="abs main-nav"><span>HOME</span><span>SERVICES</span><span>ABOUT US</span><span>CONTACT US</span></nav>
  <div class="abs header-phone">
    <span class="phone-dot"><svg width="16" height="16" viewBox="0 0 24 24"><path fill="#fff" d="M6.6 10.8a15.1 15.1 0 0 0 6.6 6.6l2.2-2.2c.3-.3.7-.4 1-.2 1.1.4 2.3.6 3.6.6.6 0 1 .4 1 1V20c0 .6-.4 1-1 1A17 17 0 0 1 3 4c0-.6.4-1 1-1h3.5c.6 0 1 .4 1 1 0 1.3.2 2.5.6 3.6.1.3 0 .7-.2 1z"/></svg></span>
    555-014-2286
  </div>
</header>

<section class="hero">
  <div class="abs hero-photo" role="img" aria-label="Renovated kitchen with stainless appliances, grey cabinets and a blue wall"></div>
  <div class="abs hero-ring"></div>
  <div class="abs hero-badge">
    <div class="hero-title">YOUR DREAM<br>LUXURY<br>RENOVATION</div>
    <span class="btn btn-light">CONTACT US</span>
  </div>
  <svg class="abs hero-arrow" style="left:22px" viewBox="0 0 20 40"><path d="M17 3 3 20l14 17" fill="none" stroke="#fff" stroke-width="3"/></svg>
  <svg class="abs hero-arrow" style="left:1158px" viewBox="0 0 20 40"><path d="M3 3l14 17L3 37" fill="none" stroke="#fff" stroke-width="3"/></svg>
  <div class="abs scroll-label">SCROLL</div>
  <svg class="abs" style="left:0;top:680px" width="1200" height="160" viewBox="0 0 1200 160">
    <path d="M0 150 Q600 -10 1200 150" fill="none" stroke="var(--orange)" stroke-width="8"/>
    <path d="M0 160 L0 160 Q600 10 1200 160 Z" fill="#fff"/>
    <path d="M590 90l10 10 10-10" fill="none" stroke="var(--ink)" stroke-width="2"/>
  </svg>
</section>

<section class="abs welcome">
  <h1 class="heading">WELCOME TO LINDCROFT MEADOW HOMES</h1>
  <p>When you want affordable, quality home construction services; think of us to do the job. Since 1981 Warren Ashby has built and remodeled over 400 homes and businesses. Let us be your contractor for the next project you start. When quality, value and personal attention to detail are important. With over 20 years experience in residential and commercial construction, you can trust your project to Lindcroft Meadow Homes.<br>"DON'T TINKER AROUND"<br>I have built my business with a partnership of clients, employees, sub-contractors, suppliers and inspectors. Since each project is unique, this partnership brings creative ideas to your home. I have deep "hands on" history in construction from foundations to final finishing touches.</p>
</section>

<section>
  <svg class="abs services-band" viewBox="0 0 1200 780" preserveAspectRatio="none">
    <defs><linearGradient id="dk" x1="0" y1="0" x2="0" y2="1"><stop offset="0" stop-color="#2a2a2a"/><stop offset="1" stop-color="#3a3a3a"/></linearGradient></defs>
    <path d="M0 30 Q600 -30 1200 30 L1200 700 Q600 800 0 700 Z" fill="url(#dk)"/>
  </svg>
  <h2 class="abs heading services-title">COMMERCIAL AND<br>RESIDENTIAL CONTRACTING</h2>
  <ul class="abs service-list" style="left:120px">
    <li>"ALL IN ONE PACKAGE"</li><li>Pre Construction Consultation</li><li>New Construction</li><li>Remodeling / Kitchens and baths</li>
  </ul>
  <ul class="abs service-list" style="left:380px">
    <li>Additions</li><li>Porches and Decks</li><li>Specializing in historic renovations</li>
  </ul>
  <p class="abs services-copy">Providing services for roofing, window replacement, electrical, air conditioning and plumbing upgrades, painting, gutters, concrete work, flooring and finish carpentry.</p>
  <span class="abs btn btn-book">BOOK NOW</span>
  <div class="abs services-photo" role="img" aria-label="Finished kitchen with wood cabinets and pendant lights"></div>
</section>

<section>
  <h2 class="abs heading projects-title">RECENT PROJECTS</h2>
  <div class="abs project" style="left:80px;width:340px;background:linear-gradient(135deg,#6d6a66,#3e3b38)" role="img" aria-label="Remodeled bathroom">BATHROOM</div>
  <div class="abs project" style="left:432px;width:348px;background:linear-gradient(135deg,#2f4a66,#5a4a3a)" role="img" aria-label="Remodeled kitchen">KITCHEN</div>
  <div class="abs project" style="left:792px;width:348px;background:linear-gradient(135deg,#7c6f62,#4a4036)" role="img" aria-label="Residential interior with polished floors">RESIDENTIAL</div>
  <div class="abs dots"><div class="dot-row"><span class="dot on"></span></div><div class="dot-row"><span class="dot"></span><span class="dot"></span></div></div>
</section>

<section>
  <svg class="abs contact-band" viewBox="0 0 1200 640" preserveAspectRatio="none">
    <path d="M0 0 H1200 V540 Q900 540 620 600 L600 620 L580 600 Q300 540 0 540 Z" fill="var(--orange)"/>
  </svg>
  <h2 class="abs heading contact-title">CONTACT US</h2>
  <div class="abs contact-phones">
    <span><span class="phone-dot"><svg width="16" height="16" viewBox="0 0 24 24"><path fill="#fff" d="M6.6 10.8a15.1 15.1 0 0 0 6.6 6.6l2.2-2.2c.3-.3.7-.4 1-.2 1.1.4 2.3.6 3.6.6.6 0 1 .4 1 1V20c0 .6-.4 1-1 1A17 17 0 0 1 3 4c0-.6.4-1 1-1h3.5c.6 0 1 .4 1 1 0 1.3.2 2.5.6 3.6.1.3 0 .7-.2 1z"/></svg></span>555-014-2286</span>
    <span><span class="phone-dot"><svg width="16" height="16" viewBox="0 0 24 24"><path fill="#fff" d="M6.6 10.8a15.1 15.1 0 0 0 6.6 6.6l2.2-2.2c.3-.3.7-.4 1-.2 1.1.4 2.3.6 3.6.6.6 0 1 .4 1 1V20c0 .6-.4 1-1 1A17 17 0 0 1 3 4c0-.6.4-1 1-1h3.5c.6 0 1 .4 1 1 0 1.3.2 2.5.6 3.6.1.3 0 .7-.2 1z"/></svg></span>555-019-4471</span>
  </div>
  <div class="abs field" style="left:200px;top:2664px;width:396px;height:40px">First Name*</div>
  <div class="abs field" style="left:612px;top:2664px;width:396px;height:40px">Last Name*</div>
  <div class="abs field" style="left:200px;top:2720px;width:396px;height:40px">Email address*</div>
  <div class="abs field" style="left:612px;top:2720px;width:396px;height:40px">Phone*</div>
  <div class="abs field" style="left:200px;top:2776px;width:808px;height:112px">Message</div>
  <span class="abs btn btn-send">SEND</span>
</section>

<footer>
  <nav class="abs footer-nav"><span>HOME</span><span>SERVICES</span><span>ABOUT US</span><span>CONTACT</span></nav>
  <p class="abs copyright">© 2017 Lindcroft Meadow Homes &nbsp;|&nbsp; Legal &nbsp;|&nbsp; Terms of Use</p>
  <div class="abs social"><span></span><span></span><span></span></div>
</footer>

</body>
</html>
```